VORLAND COMPOSITES INC website in USA

VORLAND COMPOSITES INC incorporated and operated in USA needs a completely new design of website. This Wyoming based company is a importer and distributor of composites material to supply mainly to American and Canadian/Mexican customers. Our main products includes Carbon Fiber, Aramid Fiber, Glass Fiber, Basalt Fiber, High Silica Glass, Quartz Fiber, S-Glass, Alumina Fiber, Vacuum Auxiliary.

We are one stop composites solution provider for Automotive, Aerospace, Construction, Electrical and Machinery industries.

We are exclusive sales company in North America for BLORAN composites produced from China and their other Asia facilities.

Target Market(s)

USA and Canada

Industry/Entity Type

Composites materials

Coding

Coded - Design and coding required

Number of Pages Required

5+ page

Requirements
Nice to have
• Color theme to match our corporate logo VORLAND. VORLAND stands for Northgate Provisioning Trade Holdings

```html
<!DOCTYPE html>
<html lang="en">
<head>
<meta charset="utf-8">
<title>VORLAND COMPOSITES INC</title>
<link href="https://fonts.googleapis.com/css2?family=Inter:wght@400;500;600;700;800&display=swap" rel="stylesheet">
<style>
:root{
  --backdrop:#cfcfcf;
  --bg:#0a0f16;
  --nav:#0b0e13;
  --card:#0d1520;
  --card-line:#1a2532;
  --text:#ffffff;
  --muted:#cfd6de;
  --accent:#22d3ee;
  --accent2:#2fe6d0;
  --link:#3bc3f0;
  --chip:#111a24;
}
*{box-sizing:border-box;margin:0;padding:0}
html,body{width:709px;height:1200px;overflow:hidden;background:var(--backdrop)}
body{font-family:"Inter",Arial,sans-serif;color:var(--text)}
.page{position:absolute;left:48px;top:48px;width:1284px;height:2311px;background:var(--bg);transform:scale(0.4778);transform-origin:0 0;overflow:hidden}
.wrap{position:absolute;left:190px;width:904px}
.nav{position:absolute;left:0;top:0;width:1284px;height:50px;background:var(--nav)}
.brand{position:absolute;left:192px;top:6px;display:flex;align-items:center;gap:8px}
.brand-dot{width:38px;height:38px;border-radius:50%;border:2px solid #e5e7eb}
.brand-name{font-size:12px;font-weight:700;color:var(--accent);letter-spacing:.2px}
.brand-sub{font-size:7.5px;color:#9aa4ae;margin-top:3px}
.menu{position:absolute;right:174px;top:12px;display:flex;align-items:center;gap:14px;font-size:11px;color:var(--link)}
.menu .current{background:#1c2733;color:#c9d3dc;border-radius:4px;padding:6px 8px;font-size:9px}
.menu .quote{background:var(--accent);color:#04202a;font-weight:600;border-radius:4px;padding:7px 7px}
.hero{position:absolute;left:0;top:50px;width:1284px;height:670px;background:linear-gradient(180deg,#3e4656 0%,#5a5c68 30%,#4d4a50 55%,#5c5049 75%,#3a3a3f 100%)}
.hero-copy{position:absolute;left:0;top:0;width:100%;text-align:center}
.badge{display:inline-block;margin-top:142px;background:#121a23;border-radius:16px;padding:7px 16px;font-size:12px}
.hero h1{font-size:44px;font-weight:800;line-height:58px;margin-top:8px;letter-spacing:-.3px}
.hero h1 .hl{color:var(--accent2)}
.lede{font-size:15px;margin-top:8px}
.ctas{display:flex;justify-content:center;gap:11px;margin-top:24px}
.btn{width:190px;height:48px;border-radius:24px;font-size:14px;font-weight:700;display:flex;align-items:center;justify-content:center}
.btn-solid{background:linear-gradient(90deg,#3ff0d7,#22d3ee);color:#07242c}
.btn-ghost{border:2px solid var(--accent);color:#fff}
.pills{display:flex;justify-content:center;gap:10px;margin-top:40px}
.pill{background:#121a23;border-radius:16px;padding:8px 16px;font-size:12px}
.sec-title{font-size:22px;font-weight:700}
.tags{position:absolute;right:0;top:12px;display:flex;gap:6px}
.tag{border:1px solid #2a3644;border-radius:10px;padding:4px 7px;font-size:7.5px;color:#aab4be}
.grid{display:grid;grid-template-columns:repeat(3,291px);gap:16px}
.card{background:var(--card);border:1px solid var(--card-line);border-radius:6px;padding:18px 13px}
.icon{width:56px;height:56px;border-radius:6px;background:linear-gradient(135deg,#22d3ee,#1aa6c4 60%,#0d1520);opacity:.85}
.card h3{font-size:15px;font-weight:700;margin-top:12px}
.card p{font-size:10px;line-height:17px;color:var(--muted);margin-top:8px}
.divider{position:absolute;left:0;width:1284px;height:1px;background:#141c26}
.catalog{position:absolute;right:0;top:0;border:1px solid #2a3644;border-radius:16px;padding:9px 12px;font-size:10px;font-weight:600}
.cta-band{position:absolute;left:174px;top:1546px;width:921px;height:62px;background:linear-gradient(90deg,#0f1923,#0c141d);border-radius:6px}
.cta-band p{position:absolute;left:14px;top:24px;font-size:10px}
.cta-band .talk{position:absolute;right:0;top:14px;background:var(--accent);color:#04202a;border-radius:16px;padding:9px 12px;font-size:10px;font-weight:600}
.footer .col-title{font-size:15px;font-weight:600;color:#b8c0c8;padding-bottom:12px;border-bottom:1px solid #1c2530;width:218px}
.footer ul{list-style:none;margin-top:12px}
.footer li{font-size:10px;line-height:25px;color:var(--link)}
.footer .plain{color:#e5e7eb}
.footer .fine{font-size:7px;color:#aab4be;line-height:16px}
</style>
</head>
<body>
<div class="page">
  <header class="nav">
    <div class="brand">
      <span class="brand-dot"></span>
      <div><div class="brand-name">VORLAND COMPOSITES INC</div><div class="brand-sub">Wyoming · North America Distributor</div></div>
    </div>
    <nav class="menu">
      <span class="current">Home</span><span>Products</span><span>Industries</span><span>About</span><span>Contact</span><span class="quote">Request a Quote</span>
    </nav>
  </header>

  <section class="hero">
    <div style="position:absolute;inset:0" role="img" aria-label="City skyline at dusk above rows of composite fabric rolls on a road"></div>
    <div class="hero-copy">
      <span class="badge">Exclusive BLORAN Partner · USA · Canada · Mexico</span>
      <h1>One-stop composites supply for<br><span class="hl">Aerospace, Automotive, Construction &amp; Energy</span></h1>
      <p class="lede">Stock + custom weaves, unidirectional, multiaxials, and high-temp fibers with technical documentation, QA traceability, and North American logistics.</p>
      <div class="ctas"><span class="btn btn-solid">BROWSE PRODUCTS</span><span class="btn btn-ghost">REQUEST A QUOTE</span></div>
      <div class="pills"><span class="pill">Carbon • Aramid • Glass • Basalt</span><span class="pill">High Silica • Quartz • S-Glass</span><span class="pill">Alumina • Vacuum Auxiliary</span></div>
    </div>
  </section>

  <section class="wrap" style="top:752px">
    <h2 class="sec-title">Why VORLAND</h2>
    <div class="tags"><span class="tag">Certs &amp; COAs</span><span class="tag">Rapid Lead Times</span><span class="tag">Multi-Industry Expertise</span></div>
    <div class="grid" style="margin-top:24px">
      <div class="card" style="height:187px"><div class="icon" role="img" aria-label="Access icon"></div><h3>Exclusive BLORAN Access</h3><p>Priority access to BLORAN composite lines manufactured in Asia with QA traceability and export documentation tuned for North America.</p></div>
      <div class="card" style="height:187px"><div class="icon" role="img" aria-label="Catalog icon"></div><h3>Engineering-grade Catalog</h3><p>From PAN-based carbon to high-temperature silica and alumina fibers, our breadth covers performance, process, and budget envelopes.</p></div>
      <div class="card" style="height:187px"><div class="icon" role="img" aria-label="Processing icon"></div><h3>Vacuum &amp; Processing</h3><p>Vacuum bagging films, peel plies, release media, and ancillary supplies for prepreg, infusion, and OOA processes—bundled to your BOM.</p></div>
    </div>
  </section>
  <div class="divider" style="top:1028px"></div>

  <section class="wrap" style="top:1064px">
    <h2 class="sec-title">Core Product Families</h2>
    <span class="catalog">Full catalog</span>
    <div class="grid" style="margin-top:22px">
      <div class="card" style="height:170px"><div class="icon" role="img" aria-label="Carbon fiber icon"></div><h3>Carbon Fiber</h3><p>Woven, UD, multiaxial, and prepreg-ready reinforcements for structural applications.</p></div>
      <div class="card" style="height:170px"><div class="icon" role="img" aria-label="Aramid fiber icon"></div><h3>Aramid Fiber</h3><p>Impact-resistant fabrics for ballistic and abrasion environments.</p></div>
      <div class="card" style="height:170px"><div class="icon" role="img" aria-label="Glass icon"></div><h3>Glass &amp; S-Glass</h3><p>E-glass and S-glass options balancing cost and performance.</p></div>
      <div class="card" style="height:170px"><div class="icon" role="img" aria-label="Basalt fiber icon"></div><h3>Basalt Fiber</h3><p>Naturally derived high-strength fibers with thermal stability.</p></div>
      <div class="card" style="height:170px"><div class="icon" role="img" aria-label="Silica and quartz icon"></div><h3>High Silica &amp; Quartz</h3><p>High-temperature and dielectric-stable reinforcements.</p></div>
      <div class="card" style="height:170px"><div class="icon" role="img" aria-label="Alumina fiber icon"></div><h3>Alumina Fiber</h3><p>Ceramic fibers for extreme heat and wear environments.</p></div>
    </div>
  </section>
  <div class="divider" style="top:1508px"></div>

  <div class="cta-band">
    <p><strong>Need specification support?</strong> Our team can map your mechanical targets to the right fiber/weave and process route.</p>
    <span class="talk">Talk to Engineering</span>
  </div>
  <div class="divider" style="top:1646px"></div>

  <section class="wrap" style="top:1682px">
    <h2 class="sec-title">Industries Served</h2>
    <div class="grid" style="margin-top:22px">
      <div class="card" style="height:170px"><div class="icon" role="img" aria-label="Aerospace icon"></div><h3>Aerospace</h3><p>Prepreg, OOA, autoclave, and interior panels.</p></div>
      <div class="card" style="height:170px"><div class="icon" role="img" aria-label="Automotive icon"></div><h3>Automotive</h3><p style="padding-right:20px">Body panels, monocoques, interior trims, and tooling.</p></div>
      <div class="card" style="height:170px"><div class="icon" role="img" aria-label="Construction icon"></div><h3>Construction</h3><p>Rebar wraps, FRP plates, strengthening systems.</p></div>
      <div class="card" style="height:153px"><div class="icon" role="img" aria-label="Electrical icon"></div><h3>Electrical</h3><p>Dielectric laminates and thermal insulation stacks.</p></div>
      <div class="card" style="height:153px"><div class="icon" role="img" aria-label="Machinery icon"></div><h3>Machinery</h3><p>Lightweight arms, guards, and high-temp housings.</p></div>
      <div class="card" style="height:153px"><div class="icon" role="img" aria-label="Energy icon"></div><h3>Energy</h3><p>Wind blades, tanks, and insulation jackets.</p></div>
    </div>
  </section>
  <div class="divider" style="top:2110px"></div>

  <footer class="wrap footer" style="top:2136px;height:150px">
    <div class="brand" style="left:0;top:0">
      <span class="brand-dot"></span>
      <div><div class="brand-name">VORLAND COMPOSITES INC</div><div class="brand-sub">Wyoming · North America Distributor</div></div>
    </div>
    <p style="position:absolute;left:0;top:52px;font-size:10px;color:#c2cad2">Exclusive North America sales partner for BLORAN Composites.</p>
    <div style="position:absolute;left:452px;top:0">
      <div class="col-title">Explore</div>
      <ul><li>Product Catalog</li><li>Industries</li><li>About</li><li>Contact</li></ul>
    </div>
    <div style="position:absolute;left:686px;top:0">
      <div class="col-title">Head Office</div>
      <ul><li class="plain">Cheyenne, WY, USA</li><li>sales@vorlandcomposites.com</li><li>+1 (307) 555-0476</li><li class="fine">© 2025 VORLAND COMPOSITES INC. All rights reserved.</li></ul>
    </div>
  </footer>
</div>
</body>
</html>
```